Commercial Refrigeration Service Company requires stylish and fresh looking flyer.

We need a flyer to hand out to new customers. It should have a photo and our branding, list all the services that are offered and our contact details.
We would like two flyers to be supplied, both identical though one offering a discount until July ( Half Price Service Fee ). The flyer should be clear, interesting and in similar colours to the branding package supplied.
Please look at our website for information about the services on offer:
www.brisko-coolworks.com.au

Target Market(s)

Cafes, bars, restaurants, pubs ect.

Font styles to use
Other font styles liked:
• Font package provided

Colors
85cae6
ffffff
333333

Requirements
Must have
• - The photo provided.
• - The company logo.
• - Similar feel to the website & business card.
• - Smooth layout and clear to understand.
Should not have
• - No clunky badges or prints.

```html
<!DOCTYPE html>
<html lang="en">
<head>
<meta charset="utf-8">
<title>Brisko Coolworks – Service Flyer</title>
<link rel="stylesheet" href="https://fonts.googleapis.com/css2?family=Didact+Gothic&family=Hind:wght@500;600;700&display=swap">
<style>
  :root {
    --brand-blue: #5bc2ea;
    --ink: #333333;
    --black: #0a0a0a;
    --paper-top: #f5f5f5;
    --paper-bottom: #e3e3e3;
    --backdrop: #4a4a4a;
  }
  * { box-sizing: border-box; margin: 0; padding: 0; }
  html, body { width: 1200px; height: 1146px; overflow: hidden; background: var(--backdrop); }
  .flyer {
    position: absolute; left: 195px; top: 0; width: 810px; height: 1146px;
    background: linear-gradient(var(--paper-top), var(--paper-bottom));
    font-family: "Didact Gothic", sans-serif; color: var(--ink); overflow: hidden;
  }
  .hero-photo {
    position: absolute; left: 0; top: 0; width: 810px; height: 322px;
    background: linear-gradient(180deg, #b9d4ea 0%, #9fb3c2 45%, #6d7178 75%, #5b5d61 100%);
  }
  .brand-band {
    position: absolute; left: 0; top: 322px; width: 810px; height: 163px;
    background: var(--brand-blue); text-align: center;
  }
  .brand-name {
    position: absolute; left: 0; right: 0; top: 26px;
    font-size: 58px; letter-spacing: 52px; text-indent: 52px; color: var(--ink);
  }
  .brand-dot {
    position: absolute; left: 397px; top: 114px; width: 16px; height: 16px;
    border: 2px solid var(--ink); border-radius: 50%;
  }
  .tagline { position: absolute; left: 0; right: 0; text-align: center; }
  .tagline-small { top: 502px; font-size: 12px; letter-spacing: 4px; }
  .tagline-small::before, .tagline-small::after {
    content: ""; display: inline-block; width: 28px; height: 1px; background: var(--ink);
    vertical-align: middle; margin: 0 16px;
  }
  .tagline-large { top: 526px; font-size: 23px; letter-spacing: 9px; text-indent: 9px; }
  .offer {
    position: absolute; left: 133px; top: 588px; width: 543px; height: 120px;
    border: 1.5px dotted #777; text-align: center; color: var(--brand-blue);
  }
  .offer-title { margin-top: 14px; font-size: 52px; line-height: 56px; letter-spacing: -0.5px; }
  .offer-sub { font-size: 25px; line-height: 30px; }
  .services { position: absolute; left: 0; right: 0; top: 744px; text-align: center; font-family: "Hind", sans-serif; }
  .services-heading { font-size: 25px; font-weight: 700; color: var(--ink); line-height: 30px; }
  .services-heading .dots { color: var(--brand-blue); font-size: 12px; letter-spacing: 6px; vertical-align: middle; }
  .services-list { list-style: none; margin-top: 4px; color: var(--brand-blue); font-size: 23px; font-weight: 600; line-height: 26px; }
  .ornament {
    position: absolute; left: 378px; top: 886px; width: 54px; height: 54px;
    background: radial-gradient(circle, #cfcfcf 0%, rgba(207,207,207,0) 70%);
  }
  .details { position: absolute; left: 0; right: 0; top: 968px; text-align: center; font-size: 20px; line-height: 24px; }
  .details .web { font-family: "Hind", sans-serif; font-weight: 700; font-size: 21px; margin-top: 2px; }
  .social { position: absolute; left: 0; right: 0; top: 1062px; text-align: center; }
  .social span { display: inline-block; width: 22px; height: 22px; border-radius: 50%; background: var(--ink); margin: 0 1px; }
  .contact-bar { position: absolute; left: 0; bottom: 0; width: 810px; height: 42px; }
  .contact-text { position: absolute; top: 1112px; font-size: 20px; font-family: "Hind", sans-serif; font-weight: 500; }
  .contact-phone { left: 166px; color: var(--brand-blue); }
  .contact-email { left: 343px; color: var(--black); }
</style>
</head>
<body>
<main class="flyer">
  <div class="hero-photo" role="img" aria-label="Photo of the technician leaning on the branded service ute parked by the beach"></div>

  <header class="brand-band">
    <div class="brand-name">BRISKO</div>
    <span class="brand-dot"></span>
  </header>

  <p class="tagline tagline-small">COMMERCIAL</p>
  <p class="tagline tagline-large">REFRIGERATION</p>

  <section class="offer">
    <h1 class="offer-title">DISCOUNT UNTIL JULY</h1>
    <p class="offer-sub">PAY ONLY HALF PRICE OF THE SERVICE FEE</p>
  </section>

  <section class="services">
    <h2 class="services-heading"><span class="dots">• • •</span> OUR SERVICES <span class="dots">• • •</span></h2>
    <ul class="services-list">
      <li>COMMERCIAL REFRIGERATION</li>
      <li>ICE MAKERS | BEER SYSTEMS | ELECTRICAL</li>
      <li>24HR SERVICE | SALES | INSTALLATION</li>
    </ul>
  </section>

  <div class="ornament" role="img" aria-label="Small snowflake ornament"></div>

  <address class="details" style="font-style:normal">
    <p>PO Box 1180 Seabreeze NSW 2099</p>
    <p>ABN: 12 345 678 901 &nbsp;|&nbsp; Licence No: 100234A</p>
    <p class="web">WWW.BRISKO-COOLWORKS.COM.AU</p>
  </address>

  <div class="social" aria-label="Social media links"><span></span><span></span><span></span></div>

  <svg class="contact-bar" viewBox="0 0 810 42" aria-hidden="true">
    <rect x="0" y="36" width="150" height="6" fill="var(--black)"/>
    <polygon points="129,42 150,0 325,0 325,42" fill="var(--black)"/>
    <polygon points="325,0 662,0 682,36 810,36 810,42 325,42" fill="var(--brand-blue)"/>
    <g transform="translate(148,14)" fill="var(--brand-blue)">
      <path d="M1 5 Q8 -1 15 5 L12 7 Q8 4 4 7 Z"/>
      <rect x="2" y="7" width="12" height="8" rx="1"/>
    </g>
    <g transform="translate(344,15)">
      <rect x="0" y="0" width="16" height="11" fill="var(--black)"/>
      <path d="M0 0 L8 6 L16 0" stroke="var(--brand-blue)" stroke-width="1.3" fill="none"/>
    </g>
  </svg>
  <span class="contact-text contact-phone">0412 555 018</span>
  <span class="contact-text contact-email" style="left:364px">Info@brisko-coolworks.com.au</span>
</main>
</body>
</html>
```